Creation of a construction/bricklaying business website

Following the template format of "Halloway 7", the following content would need to be included:
1. Landing page with 3 tiles that go to their own pages.
- Landing page to include background photo and description of services offered.
2. 3 tiles to include:
a) "Contact Us For A Free Quote or Friendly Discussion" Form (middle tile)
b) Case Studies and Testimonials
c) Certifications and Professional Membership
- Design logo to be used from previous SketchNestle project. Example of logo attached below, please access full JPG files from our account.

Target Market(s)

Prospective clients seeking construction work (bricklaying speciality)

Industry/Entity Type

Residential Construction

Coding

Coded - Design and coding required

Number of Pages Required

4 page

Font styles to use
Sans Serif

Colors

Designer to choose colors to be used in the design.

Requirements
Must have
• Following the template format of "Halloway 7", the following content would need to be included:
• 1. Landing parent page with 3 tiles that go to the 3 child pages.
• - Landing page to include background photo and description of services offered.
• 2. 3 tiles to include:
• a) "Contact Us For A Free Quote or Friendly Discussion" Form (middle tile)
• b) Case Studies and Testimonials (first tile / left side)
• c) Certifications and Professional Memberships (third tile / right side) (This should include logos of the relevant organisations being displayed. Specifically GQT and the Pillar Seal GQT).
• - Design logo to be used from previous SketchNestle project. Example of logo attached below, please access full JPG files from our account.
Nice to have
• Sleek and modern feel.
• Approachable in terms of how people can contact the company for a quote.
• Traditional pictures to give credibility and comfort around choosing this company.
Should not have
• Cheesy pictures
• Over-complicated
• Simple to use
• Easy URL domain name

```html
<!DOCTYPE html>
<html lang="en">
<head>
<meta charset="utf-8">
<title>R.T.Marlow Construction Ltd</title>
<link rel="stylesheet" href="https://fonts.googleapis.com/css2?family=Exo+2:wght@500;600&family=Jost:wght@400;500&display=swap">
<style>
  :root{
    --brand-blue:#1457a8;
    --footer-blue:#1459a7;
    --ink:#1c1c1c;
    --grey:#6e6e6e;
    --white:#ffffff;
    --icon-grey:#7a7a7a;
  }
  *{box-sizing:border-box;margin:0;padding:0}
  html,body{width:1152px;height:1200px;overflow:hidden;background:var(--white)}
  body{position:relative;font-family:"Jost",sans-serif;color:var(--ink)}
  .abs{position:absolute}

  .brand{font-family:"Jost",sans-serif;font-weight:500;color:var(--brand-blue);display:flex;align-items:center;gap:8px;white-space:nowrap}
  .brand-mark{width:12px;height:12px;background:var(--brand-blue)}
  .site-header .brand{left:155px;top:36px;font-size:26px}

  .contact-item{display:flex;align-items:center;gap:10px;font-size:14px;line-height:21px;color:#333}
  .icon-circle{width:36px;height:36px;border-radius:50%;background:var(--brand-blue);display:flex;align-items:center;justify-content:center;flex:none}
  .header-phone{left:608px;top:29px}
  .header-email{left:787px;top:29px}

  .hero{left:0;top:102px;width:1152px;height:460px;
    background:linear-gradient(100deg,#5d6b7c 0%,#7b8591 30%,#8b8a84 55%,#3d5f8a 72%,#c8a92a 82%,#8d8a7d 100%)}
  .hero-shade{left:0;top:102px;width:1152px;height:460px;background:rgba(20,25,35,.25)}
  .hero-title{left:150px;top:236px;width:852px;text-align:center;font-family:"Exo 2",sans-serif;font-weight:600;font-size:27px;line-height:31px;color:var(--white)}
  .service-list{left:150px;width:852px;display:flex;justify-content:center;gap:34px;list-style:none;font-family:"Exo 2",sans-serif;font-weight:500;font-size:19px;color:var(--white)}
  .service-list li::before{content:"•";margin-right:18px}
  .services-a{top:320px}
  .services-b{top:345px}
  .cta{left:500px;top:389px;width:155px;height:31px;background:var(--brand-blue);color:var(--white);font-family:"Exo 2",sans-serif;font-weight:500;font-size:16px;display:flex;align-items:center;justify-content:center;gap:6px}

  .intro .brand{left:0;width:1152px;justify-content:center;top:614px;font-size:24px}
  .intro-text{left:160px;width:832px;text-align:center;font-size:15px;line-height:23px}
  .intro-main{top:669px}
  .intro-invite{top:746px}

  .tile{top:816px;width:266px;height:183px;box-shadow:0 10px 10px -4px rgba(0,0,0,.45);display:flex;flex-direction:column;align-items:center;justify-content:flex-end;padding-bottom:38px;color:var(--white);font-family:"Exo 2",sans-serif;font-weight:500;font-size:14px;line-height:18px;text-align:center}
  .tile-cases{left:155px;background:linear-gradient(135deg,#3a3836,#22201e)}
  .tile-quote{left:443px;background:linear-gradient(135deg,#4a4038,#232120)}
  .tile-certs{left:731px;background:linear-gradient(135deg,#6a4a3c,#3b2a24)}
  .tile svg,.tile .badges{margin-bottom:10px}
  .badges{display:flex;gap:6px}
  .badge{width:34px;height:56px;background:#b3162c}
  .badge.round{width:36px;height:36px;border-radius:50%;margin-top:4px}

  .site-footer{left:0;top:1066px;width:1152px;height:134px;background:var(--footer-blue);color:var(--white)}
  .footer-side{left:0;top:1066px;width:300px;height:134px;background:#7d7d7d}
  .footer-side .brand{left:0;width:300px;justify-content:center;top:90px;font-size:22px;color:#e6e6e6}
  .footer-side .brand-mark{background:#e6e6e6}
  .site-footer .icon-circle{background:var(--icon-grey)}
  .site-footer .contact-item{color:var(--white)}
  .foot-address{left:348px;top:1105px}
  .foot-phone{left:590px;top:1105px}
  .foot-email{left:780px;top:1105px}
  .copyright{left:348px;top:1167px;font-size:13.5px;color:var(--white)}
  .social{left:790px;top:1165px;display:flex;gap:4px}
  .social span{width:24px;height:24px;border-radius:50%;background:var(--white)}
</style>
</head>
<body>
  <header class="site-header">
    <div class="brand abs"><span class="brand-mark"></span>R.T.Marlow Construction</div>
    <div class="contact-item header-phone abs">
      <span class="icon-circle"><svg width="18" height="18" viewBox="0 0 24 24"><path fill="#fff" d="M6.6 10.8a15 15 0 0 0 6.6 6.6l2.2-2.2c.3-.3.7-.4 1-.2 1.1.4 2.3.6 3.6.6.6 0 1 .4 1 1V20c0 .6-.4 1-1 1A17 17 0 0 1 3 4c0-.6.4-1 1-1h3.5c.6 0 1 .4 1 1 0 1.3.2 2.5.6 3.6.1.3 0 .7-.2 1z"/></svg></span>
      <div>Call Us On :<br>555.014.2290</div>
    </div>
    <div class="contact-item header-email abs">
      <span class="icon-circle"><svg width="20" height="14" viewBox="0 0 20 14"><rect x="1" y="1" width="18" height="12" fill="none" stroke="#fff" stroke-width="1.6"/><path d="M1 1l9 7 9-7" fill="none" stroke="#fff" stroke-width="1.6"/></svg></span>
      <div>Email<br>info@rtmarlowbuild.com</div>
    </div>
  </header>

  <section class="hero-section">
    <div class="hero abs" role="img" aria-label="Builder holding a yellow hard hat and rolled plans in front of a blurred building site"></div>
    <div class="hero-shade abs"></div>
    <h1 class="hero-title abs">R.T.Marlow Construction Ltd is a construction company that has expertise and experience in the following areas</h1>
    <ul class="service-list services-a abs"><li>Extensions</li><li>New build / New houses</li><li>Garden walls</li></ul>
    <ul class="service-list services-b abs"><li>Plastering</li><li>Brickwork</li><li>Groundworks</li></ul>
    <a class="cta abs">Contact Us Today <svg width="16" height="8" viewBox="0 0 16 8"><path d="M0 4h14M11 1l3 3-3 3" fill="none" stroke="#fff" stroke-width="1.2"/></svg></a>
  </section>

  <section class="intro">
    <div class="brand abs"><span class="brand-mark"></span>R.T.Marlow Construction</div>
    <p class="intro-text intro-main abs">We pride ourselves on attention to detail, pride in our completed project and client satisfaction. We believe in full transparency and this is reflected in the jobs we quote for you. We break down each step with both labour and materials cost so you can see exactly what you are paying for.</p>
    <p class="intro-text intro-invite abs">Feel free to get in touch and we can talk through what you are looking to achieve.</p>
  </section>

  <nav class="tiles">
    <a class="tile tile-cases abs" role="img" aria-label="Office desk scene with case study icon">
      <svg width="70" height="50" viewBox="0 0 70 50"><rect x="30" y="2" width="34" height="44" fill="none" stroke="#fff" stroke-width="2.5"/><path d="M36 14h22M36 22h16M36 30h18" stroke="#fff" stroke-width="2"/><circle cx="14" cy="32" r="10" fill="#fff"/></svg>
      Case Studies and<br>Testimonials</a>
    <a class="tile tile-quote abs" role="img" aria-label="Laptop on a desk with quote form icon">
      <svg width="56" height="56" viewBox="0 0 56 56"><path d="M10 4h26l12 12v36H10z" fill="none" stroke="#fff" stroke-width="3"/><path d="M18 22h22M22 32h18M26 42h14" stroke="#fff" stroke-width="2.5"/><path d="M4 40l5 8 9-16" fill="none" stroke="#fff" stroke-width="3"/></svg>
      Contact Us For A<br>Free Quote</a>
    <a class="tile tile-certs abs" role="img" aria-label="Bricklayer laying bricks with membership badges">
      <div class="badges"><span class="badge"></span><span class="badge round"></span></div>
      Certifications and Professional<br>Memberships</a>
  </nav>

  <footer>
    <div class="site-footer abs"></div>
    <div class="footer-side abs"><div class="brand abs"><span class="brand-mark"></span>R.T.Marlow</div></div>
    <div class="contact-item foot-address abs">
      <span class="icon-circle"><svg width="14" height="18" viewBox="0 0 14 18"><path d="M7 0a7 7 0 0 1 7 7c0 5-7 11-7 11S0 12 0 7a7 7 0 0 1 7-7z" fill="#fff"/><circle cx="7" cy="7" r="2.5" fill="#7a7a7a"/></svg></span>
      <div>Street Name, City Name<br>State Zipcode</div>
    </div>
    <div class="contact-item foot-phone abs">
      <span class="icon-circle"><svg width="18" height="18" viewBox="0 0 24 24"><path fill="#fff" d="M6.6 10.8a15 15 0 0 0 6.6 6.6l2.2-2.2c.3-.3.7-.4 1-.2 1.1.4 2.3.6 3.6.6.6 0 1 .4 1 1V20c0 .6-.4 1-1 1A17 17 0 0 1 3 4c0-.6.4-1 1-1h3.5c.6 0 1 .4 1 1 0 1.3.2 2.5.6 3.6.1.3 0 .7-.2 1z"/></svg></span>
      <div>Call Us On :<br>555.014.2290</div>
    </div>
    <div class="contact-item foot-email abs">
      <span class="icon-circle"><svg width="20" height="14" viewBox="0 0 20 14"><rect x="1" y="1" width="18" height="12" fill="none" stroke="#fff" stroke-width="1.6"/><path d="M1 1l9 7 9-7" fill="none" stroke="#fff" stroke-width="1.6"/></svg></span>
      <div>Email<br>info@rtmarlowbuild.com</div>
    </div>
    <p class="copyright abs">Copyright ©2018 R.T.Marlow Construction Ltd. All Rights Reserved.</p>
    <div class="social abs" aria-label="Social links"><span></span><span></span><span></span><span></span></div>
  </footer>
</body>
</html>
```